Very basic draft completed. Need someone to apply their creative magic

I am building a new website for my business and looking for a designer to assist me on a part-time basis.

My business is a booking site for classes and lessons. It is essentially a directory service, and needs to conform to a standard web-layout that is easy to navigate and familiar to users (i.e. nothing to creative). The function and structure i have adopted is common amongst sites like zulk, hotel booking services, etc.

The first task on my list is to develop the main page. I have already compiled a draft of the first page using Fireworks (see attached) and am looking for someone to cast their creative magic to this draft while maintaining the general layout of the page. After the main page is developed, I will be looking for the same designer to assist with the rest of the site.

Design wise, I'd like to go for a slightly retro feel
By this I mean a moderately modern page with a spark of retro here and there. If you look at my draft you'll notice that I've used regular font for most text, and retro/old-school fonts for surburb names.

I happy for you to suggest colours, but regular page elements such as web links need to remain standard (i.e links = blue) so that they are familiar and identifiable to my users.

Other points:
1) I don't want the page to be too dark (dark headings, images and borders are fine, but I'd like to maintain white or light backgrounds)

2) Positioning: The Body should be centred, with the Header and Footer extending across the hole screen (as illustrated in my draft)

3) I'm happy if the design includes images from photostock libraries.The Silhoute picture for my draft were choosen because there are hundreds of them, and I can regularly change them on the site - keeping it fresh and new. I'd be very happy if the design incorporate images that could also be place often using photo stock images (i.e. happy to keep silhoutes, but leave it to you to decide what looks best)

Note: I'm happy for you to "copy" art work from any photo stock site, and I will pay for the full quality images when the design is selected.

4) The page Footer needs a lot of attention. It will contain standard Footer links/elements.

5) You are free to do anything to the Header section. It needs to have login/register elements

I'm happy to provide further comments, or review other sites/work to help direct design work.

Hi All,

I've updated the project brief, eliminating many of the requirements and giving you the freedom with design submissions, etc. I've also added the $20 payment for submissions. 
Cheers,
Corbin

Reason: I'm away on holiday and will review your submissions and provide feedback when I get back.

```html
<!DOCTYPE html>
<html lang="en">
<head>
<meta charset="utf-8">
<title>Step Out Studio – Classes and Lessons</title>
<link href="https://fonts.googleapis.com/css2?family=Arimo:ital,wght@0,400;0,700;1,400&family=Baumans&family=Special+Elite&display=swap" rel="stylesheet">
<style>
:root{
  --ink:#222;--muted:#555;--link:#1f5fbf;--red:#c8171b;--dark:#141414;--band:#2a0c0c;
  --blue:#3d7fc9;--blue-dark:#1f5a9f;--panel:#dde6ef;--panel-line:#b9c9da;--pink:#fbeef0;
  --page:#e9e8e4;--white:#fff;
}
*{box-sizing:border-box;margin:0;padding:0}
html,body{width:1067px;height:1200px;overflow:hidden}
body{position:relative;font-family:"Arimo",Arial,sans-serif;color:var(--ink);font-size:11px;
  background:linear-gradient(#c9c8c4 116px,#f3f2ef 300px,var(--page) 990px)}
a{color:var(--link);text-decoration:none}
.abs{position:absolute}
/* top strip */
.topbar{position:absolute;left:0;top:0;width:1067px;height:22px;background:#1a0606}
.toplinks{position:absolute;left:181px;top:6px;font-size:8px;color:#ddd;font-style:italic;word-spacing:2px}
.tophelp{position:absolute;left:640px;top:4px;color:#fff;font-weight:700;font-size:10px;display:flex;gap:10px;align-items:center}
.flag{width:11px;height:8px;background:#c33;display:inline-block;border:1px solid #fff}
/* header */
.header{position:absolute;left:0;top:22px;width:1067px;height:64px;background:linear-gradient(#d5d9de,#8c939c)}
.brand{position:absolute;left:170px;top:30px;display:flex;align-items:center;gap:10px}
.brand-mark{width:26px;height:26px;background:var(--ink)}
.brand-name{font-family:"Arimo",Arial,sans-serif;font-weight:700;color:var(--ink);font-size:30px;line-height:1}
.tagline{position:absolute;left:248px;top:65px;font-size:11px;font-style:italic;color:#222}
.figures{position:absolute;left:458px;top:8px;width:190px;height:50px;background:linear-gradient(90deg,#ccc,#999);opacity:.5}
.search{position:absolute;left:771px;top:9px;width:122px;height:16px;background:var(--white);border-radius:8px;font-size:7px;color:#666;padding:3px 6px}
.search b{position:absolute;right:0;top:0;height:16px;width:22px;background:#222;color:#fff;border-radius:0 8px 8px 0;font-size:8px;text-align:center;line-height:16px}
.login{position:absolute;left:671px;top:43px;font-size:8px;color:#fff;font-weight:700;display:flex;gap:6px;align-items:center}
.login i{display:inline-block;width:55px;height:14px;background:#e5ebf1;border-radius:3px}
.login em{font-style:normal;background:#222;padding:2px 4px;border-radius:2px}
/* nav */
.nav{position:absolute;left:0;top:86px;width:1067px;height:30px;background:linear-gradient(#3a3a3a,#0d0d0d)}
.nav ul{list-style:none;display:flex;position:absolute;left:229px;top:0;height:30px;align-items:center;gap:10px}
.nav li{color:#fff;font-weight:700;font-size:8.5px}
.nav li.on{background:var(--red);padding:6px 10px;border-radius:2px 2px 0 0}
/* body container */
.container{position:absolute;left:167px;top:130px;width:738px;height:868px;background:var(--white);border-radius:16px 16px 0 0;box-shadow:0 0 6px rgba(0,0,0,.15)}
.hero{position:absolute;left:175px;top:137px;width:723px;height:127px;border-radius:12px 12px 0 0;
  background:linear-gradient(90deg,#6d7468 0 19%,#b24a1a 19% 49%,#c46a2a 49% 68%,#3a3535 68%)}
.explore{position:absolute;left:175px;top:264px;width:723px;height:34px;background:#1e1e1e;color:#eee;font-size:9px;line-height:11px}
.explore h2{position:absolute;left:40px;top:3px;font-family:"Baumans",sans-serif;font-weight:400;color:#8fb6e6;font-size:24px;font-style:italic}
.explore p{position:absolute;left:158px;top:6px;width:440px}
.filter{position:absolute;left:175px;top:298px;width:723px;height:47px;background:#efefef;font-size:7px;color:#333}
.field{display:inline-block;border:1px solid #999;background:#fff;height:13px;font-size:7px;padding:2px 3px}
.cb{display:inline-block;width:9px;height:9px;border:1px solid #888;background:#fff;vertical-align:middle;margin-right:3px}
.btn{position:absolute;left:668px;top:17px;width:42px;height:15px;border:1px solid #999;border-radius:3px;background:linear-gradient(#fff,#ddd);text-align:center;line-height:13px;font-weight:700;font-size:8px}
/* sidebar */
.side-head{position:absolute;left:176px;top:352px;width:140px;height:21px;background:linear-gradient(var(--blue),var(--blue-dark));color:#fff;font-weight:700;font-size:8px;padding:6px 10px;border-radius:3px 3px 0 0}
.side-list{position:absolute;left:176px;top:373px;width:140px;height:238px;background:var(--panel);border:1px solid var(--panel-line);border-top:0;border-radius:0 0 6px 6px;padding:10px 5px 0}
.side-list li{list-style:none;height:20px;border-bottom:1px solid #fff;font-size:8px;font-weight:700;color:#333;padding-left:18px;position:relative;line-height:18px}
.side-list li::before{content:"+";position:absolute;left:6px;font-size:8px}
.side-list li.open::before{content:"–"}
.side-list li.sub{font-weight:400;padding-left:32px;font-size:7px;border-bottom:0}
.side-list li.sub::before{content:""}
.refine{position:absolute;left:176px;top:620px;width:140px;height:128px;border:1px solid #ccc;border-radius:6px;background:#f6f6f6}
.refine-in{position:absolute;left:10px;top:10px;width:120px;height:112px;background:var(--panel)}
.refine-in h4{background:#c8c8c8;font-size:6px;font-weight:400;padding:2px 3px}
.slider{position:absolute;left:18px;width:76px;height:2px;background:#777}
.slider i{position:absolute;left:48px;top:-3px;width:8px;height:8px;border-radius:50%;background:var(--blue)}
.news{position:absolute;left:176px;top:757px;width:140px;height:220px;border:1px solid #ccc;border-radius:6px;background:#f7f7f7}
.news p{font-size:10px;color:#444;padding:8px 14px 0}
.news-input{position:absolute;left:10px;top:40px;width:118px;height:18px;border:1px solid #aaa;background:#fff}
.join{position:absolute;left:40px;top:63px;width:60px;height:16px;background:var(--red);color:#fff;font-weight:700;font-size:10px;text-align:center;line-height:16px;border-radius:2px}
.social{position:absolute;left:10px;width:125px;display:flex;gap:16px;align-items:center;font-size:9px;color:#333;line-height:10px}
.social i{width:22px;height:22px;border-radius:50%;background:#3b7cc4;flex:none}
/* listings */
.list-head{position:absolute;left:328px;top:348px;width:567px;height:22px;background:linear-gradient(var(--blue),var(--blue-dark));border-radius:4px 4px 0 0;color:#fff;font-size:9px}
.list-head span{position:absolute;top:7px}
.row{position:absolute;left:328px;width:567px;height:58px}
.thumb{position:absolute;left:2px;top:2px;width:48px;height:48px;background:linear-gradient(#8a6a4a,#3a2a22);box-shadow:1px 1px 2px #888}
.info{position:absolute;left:60px;top:0;width:305px;height:56px;font-size:7px;line-height:8px;color:#444}
.info h3{font-size:9px;font-weight:400;color:var(--link);margin-bottom:2px}
.info .by{font-style:italic;font-size:7px;color:#666;margin:0 0 2px 2px}
.more{position:absolute;right:12px;bottom:2px;font-size:6px;text-decoration:underline}
.sched{position:absolute;left:405px;top:0;width:48px;height:58px;font-size:5.5px;line-height:6.2px;color:#333;padding-left:4px}
.pink{background:var(--pink)}
.loc{position:absolute;left:460px;top:0;width:48px;height:58px;text-align:center;font-family:"Special Elite",monospace;font-size:7.5px;line-height:8px;padding-top:38px}
.pin{position:absolute;left:5px;top:20px;width:16px;height:16px;border-radius:3px;background:linear-gradient(#eee,#bbb)}
.price{position:absolute;left:520px;top:0;width:37px;height:58px;text-align:center;font-size:14px;font-weight:700;padding-top:18px}
.price small{display:block;font-size:5px;font-weight:400;color:#555;line-height:5px;margin-top:2px}
/* featured */
.feat-title{position:absolute;left:328px;top:833px;font-size:13px;color:#333}
.carousel{position:absolute;left:328px;top:857px;width:459px;height:121px;border:1px solid #ccc;background:#fafafa}
.slide{position:absolute;top:7px;height:88px}
.cap{position:absolute;top:102px;font-size:8px;color:#333;text-align:center}
.arrow{position:absolute;top:898px;width:22px;height:24px;background:#444;border:1px solid #222}
/* footer */
.footer-band{position:absolute;left:0;top:998px;width:1067px;height:42px;background:linear-gradient(#3a0a0a,var(--band))}
.footer-brand{position:absolute;left:143px;top:1016px;font-family:"Arimo",Arial,sans-serif;font-weight:700;color:#ddd;font-size:20px}
.fsearch{position:absolute;left:660px;top:1008px;width:195px;height:21px;background:#fff;border-radius:10px;font-size:9px;padding:5px 12px;color:#444}
.fsearch b{position:absolute;right:0;top:0;width:28px;height:21px;background:#222;color:#fff;border-radius:0 10px 10px 0;text-align:center;line-height:21px;font-weight:400;font-size:12px}
.footer{position:absolute;left:0;top:1040px;width:1067px;height:160px;background:linear-gradient(#5a5a5a,#232323)}
.badges{position:absolute;left:107px;top:1062px;width:106px;height:102px;background:#fff;border-radius:6px}
.badges i{position:absolute;left:12px;width:80px;height:18px;background:#e6e0cc;border:1px solid #c9b98a}
.fcol{position:absolute;top:1059px;color:#ddd;font-size:9px;line-height:13.4px}
.fcol h5{font-size:10px;color:#fff;margin-bottom:13px}
.fcol a{color:#7fb0ff}
.copy{position:absolute;left:726px;top:1173px;font-size:8px;color:#bbb}
</style>
</head>
<body>
<div class="topbar">
  <div class="toplinks">Account Sign In . Register . Register . About . Blog . Contact</div>
  <div class="tophelp">
    <svg width="11" height="12" viewBox="0 0 12 12"><path d="M2 1l3 2-1 2 3 3 2-1 2 3-2 2C5 11 1 7 0 3z" fill="#e2591d"/></svg>
    <span>555.010.2244</span>
    <span style="margin-left:20px;display:flex;gap:5px;align-items:center"><span style="width:18px;height:12px;border-radius:50%;background:#6bbf3a;display:inline-block"></span>Live Help</span>
    <span class="flag" style="margin-left:14px"></span><span class="flag" style="background:#34599f;margin-left:-6px"></span>
  </div>
</div>

<header class="header">
  <div class="figures" role="img" aria-label="Row of dancer silhouettes"></div>
  <div class="search">Search courses by Keyword<b>GO</b></div>
  <div class="login">username: <i></i> password: <i></i> <em>go</em></div>
</header>
<div class="brand"><span class="brand-mark"></span><span class="brand-name">Step Out Studio</span></div>
<div class="tagline">Get out and Discover something new...</div>

<nav class="nav"><ul>
  <li class="on">HOME</li><li>VISUAL ARTS</li><li>COOKING</li><li>HEALTH/LIFE</li><li>LANGUAGES</li><li>PERFORMING ARTS</li><li>PROFESSIONAL</li><li>TECH/INTERNET</li><li>ARTS &amp; SCIENCES</li>
</ul></nav>

<main>
<div class="container"></div>
<div class="hero" role="img" aria-label="Banner of dancers, musicians and performers on stage"></div>
<div class="explore"><h2>Explore</h2><p>Lorem ipsum dolor sit amet, consectetur adipiscing elit. Cras suscipit lacus dapibus ante mattis in adipiscing nibh placerat. Cras bibendum porta diam, non dignissim sapien malesuada vitae.</p></div>

<div class="filter">
  <span class="abs" style="left:230px;top:3px;font-size:5px">Optional Search Criteria <a href="#">hide</a></span>
  <span class="abs" style="left:262px;top:20px">Date from <span class="field">15/12/2011</span> to <span class="field">15/01/2012</span></span>
  <span class="abs" style="left:428px;top:12px;line-height:13px"><span class="cb"></span>Mon &nbsp;<span class="cb"></span>Wed &nbsp;<span class="cb"></span>Fri &nbsp;<span class="cb"></span>Sun<br><span class="cb"></span>Tue &nbsp;<span class="cb"></span>Thu &nbsp;<span class="cb"></span>Sat &nbsp;<span class="cb" style="background:#8bb0e0"></span>All</span>
  <span class="abs field" style="left:560px;top:17px;width:87px">Any Time of Day</span>
  <span class="btn">Filter</span>
</div>

<aside>
  <div class="side-head">Explore COURSES/ACTIVITIES</div>
  <ul class="side-list">
    <li>Visual Arts (21)</li><li>Cooking (21)</li><li>Health/Life (21)</li><li>Languages (21)</li><li>Performing Arts (21)</li><li>Professional (21)</li><li>Tech/Internet (21)</li><li class="open">Arts &amp; Sciences (21)</li>
    <li class="sub">- Sciences</li><li class="sub">- Arts</li><li class="sub">- Painting</li>
  </ul>
  <div class="refine"><div class="refine-in">
    <h4>Refine search &nbsp;(recommended)</h4>
    <span class="abs" style="left:6px;top:18px;font-size:7px">Age: &nbsp;18yrs+</span>
    <div class="slider" style="top:33px"><i></i></div>
    <span class="abs" style="left:4px;top:58px;font-size:7px">Max Price: &nbsp;$50</span>
    <div class="slider" style="top:77px"><i></i></div>
  </div></div>
  <div class="news">
    <p>Join our newsletter list to get the latest updates</p>
    <div class="news-input"></div>
    <div class="join">Join Now</div>
    <div class="social" style="top:94px"><i></i>Follow us on Chirpline</div>
    <div class="social" style="top:123px"><i></i>Become our fan on Friendpage</div>
    <div class="social" style="top:157px"><i style="background:#2b74b0"></i>Connect with us on Linkwork</div>
    <div class="social" style="top:188px"><i style="background:#e8612a"></i>Send us your email enquiries</div>
  </div>
</aside>

<section>
  <div class="list-head"><span style="left:17px">Showing: All Courses &amp; Activities&gt;</span><span style="left:405px">Schedule</span><span style="left:457px">Location</span><span style="left:524px">Price</span></div>

  <div class="row" style="top:381px"><div class="thumb" role="img" aria-label="Salsa couple dancing"></div>
    <div class="info"><h3>Salsa Patterns</h3><div class="by">with Ritmo Salsa Dance Company</div>Lorem ipsum dolor sit amet, consectetuer adipiscing elit, sed diam nonummy nibh euismod tincidunt ut laoreet dolore magna aliquam erat volutpat. Ut wisi enim ad minim veniam, quis nostrud exerci tation ullamcorper suscipit lobortis nisl ut aliquip ex...<a class="more" href="#">more</a></div>
    <div class="sched">M - 6pm<br>T - 6pm<br>W - 5pm, 7pm<br>T -<br>F - 7pm<br>S -<br>S -</div>
    <div class="loc"><span class="pin"></span>Riverbank</div><div class="price">$15<small>single session</small></div></div>

  <div class="row" style="top:443px"><div class="thumb" style="background:linear-gradient(#2a3a8a,#a07ab8)" role="img" aria-label="Ballroom dancer on stage"></div>
    <div class="info pink"><h3>Ballroom Dancing for Beginners</h3><div class="by">with Twirl Step Studios</div>Ut wisi enim ad minim veniam. Lorem ipsum dolor sit amet, consectetuer adipiscing elit, sed diam nonummy nibh euismod tincidunt ut laoreet dolore magna aliquam erat volutpat. Ut wisi enim ad minim veniam, quis nostrud exerci tation ullamcorper suscipit lobortis nisl ex...<a class="more" href="#">more</a></div>
    <div class="sched pink">M -<br>T -<br>W - 5pm<br>T -<br>F - 7pm<br>S -<br>S -</div>
    <div class="loc pink"><span class="pin"></span>OAKRIDGE</div><div class="price pink">$75<small>three sessions</small></div></div>

  <div class="row" style="top:505px"><div class="thumb" style="background:linear-gradient(#1a1a1a,#7a2020)" role="img" aria-label="Tango dancers"></div>
    <div class="info"><h3>Argentine Tango - Intermediate</h3><div class="by">with Twirl Step Studios</div>Lorem ipsum dolor sit amet, consectetuer adipiscing elit, sed diam nonummy nibh euismod tincidunt ut laoreet dolore magna aliquam erat volutpat. Ut wisi enim ad minim veniam, quis nostrud exerci tation ullamcorper suscipit lobortis nisl ut aliquip ex...<a class="more" href="#">more</a></div>
    <div class="sched">M - 6pm<br>T - 6pm<br>W - 5pm, 7pm<br>T -<br>F - 7pm<br>S -<br>S -</div>
    <div class="loc"><span class="pin"></span>MILLBROOK</div><div class="price">$36<small>single session</small></div></div>

  <div class="row" style="top:566px"><div class="thumb" style="background:linear-gradient(#c9a878,#5a4a3a)" role="img" aria-label="Pilates mat class"></div>
    <div class="info pink"><h3>Kick Your Booty Mat</h3><div class="by">with Core Line Pilates Studio</div>Lorem ipsum dolor sit amet, consectetuer adipiscing elit, sed diam nonummy nibh euismod tincidunt ut laoreet dolore magna aliquam erat volutpat. Ut wisi enim ad minim veniam, quis nostrud exerci tation ullamcorper suscipit lobortis nisl ut aliquip ex...<a class="more" href="#">more</a></div>
    <div class="sched pink">M - 6pm<br>T - 6pm<br>W - 5pm, 7pm<br>T -<br>F - 7pm<br>S -<br>S -</div>
    <div class="loc pink"><span class="pin"></span>CENTRE PARK</div><div class="price pink">$105<small>four sessions</small></div></div>

  <div class="row" style="top:628px"><div class="thumb" style="background:linear-gradient(#d8c0a0,#6a5040)" role="img" aria-label="Pilates class in studio"></div>
    <div class="info"><h3>Pilates Mat Essentials</h3><div class="by">with Core Line Pilates Studio</div>Lorem ipsum dolor sit amet, consectetuer adipiscing elit, sed diam nonummy nibh euismod tincidunt ut laoreet dolore magna aliquam erat volutpat. Ut wisi enim ad minim veniam, quis nostrud exerci tation ullamcorper suscipit l.<a class="more" href="#">more</a></div>
    <div class="sched">M - 6pm<br>T - 6pm<br>W - 5pm, 7pm<br>T -<br>F - 7pm<br>S -<br>S -</div>
    <div class="loc"><span class="pin"></span>HILLSIDE</div><div class="price">$22<small>single session</small></div></div>

  <div class="row" style="top:689px"><div class="thumb" style="background:linear-gradient(#2a3a8a,#a07ab8)" role="img" aria-label="Ballroom dancer on stage"></div>
    <div class="info pink"><h3>Ballroom Dancing for Beginners</h3><div class="by">with Twirl Step Studios</div>Ut wisi enim ad minim veniam. Lorem ipsum dolor sit amet, consectetuer adipiscing elit, sed diam nonummy nibh euismod tincidunt ut laoreet dolore magna aliquam erat volutpat. Ut wisi enim ad minim veniam, quis nostrud exerci tation ullamcorper suscip nisl ut aliq ex...<a class="more" href="#">more</a></div>
    <div class="sched pink">M - 6pm<br>T - 6pm<br>W - 5pm, 7pm<br>T -<br>F - 7pm<br>S -<br>S -</div>
    <div class="loc pink"><span class="pin"></span>OAKRIDGE</div><div class="price pink">$75<small>four sessions</small></div></div>

  <div class="row" style="top:750px"><div class="thumb" role="img" aria-label="Salsa couple dancing"></div>
    <div class="info"><h3>Salsa Patterns</h3><div class="by">with Ritmo Salsa Dance Company</div>Lorem ipsum dolor sit amet, consectetuer adipiscing elit, sed diam nonummy nibh euismod tincidunt ut laoreet dolore magna aliquam erat volutpat. Ut wisi enim ad minim veniam, quis nostrud exerci tation ullamcorper suscipit lobortis nisl ut aliquip ex...<a class="more" href="#">more</a></div>
    <div class="sched">M - 6pm<br>T - 6pm<br>W - 5pm, 7pm<br>T -<br>F - 7pm<br>S -<br>S -</div>
    <div class="loc"><span class="pin"></span>Seaview</div><div class="price">$15<small>single session</small></div></div>

  <h2 class="feat-title" style="font-weight:400">Featured Courses/Activities</h2>
  <div class="carousel">
    <div class="slide" style="left:30px;width:132px;background:linear-gradient(#3a2a1a,#d8c8a8)" role="img" aria-label="Performing artists in costume"></div>
    <div class="slide" style="left:182px;width:89px;background:linear-gradient(#111,#8a6a4a)" role="img" aria-label="Musician with guitar"></div>
    <div class="slide" style="left:293px;width:136px;background:linear-gradient(#d8d0c8,#6a7a9a)" role="img" aria-label="Family cooking in kitchen"></div>
    <div class="cap" style="left:30px;width:122px">Peforming Artists (12)</div>
    <div class="cap" style="left:182px;width:89px">Musicians (32)</div>
    <div class="cap" style="left:293px;width:136px">Cooking (45)</div>
  </div>
  <div class="arrow" style="left:323px"><svg width="20" height="22"><path d="M13 6l-6 5 6 5z" fill="#fff"/></svg></div>
  <div class="arrow" style="left:768px"><svg width="20" height="22"><path d="M7 6l6 5-6 5z" fill="#fff"/></svg></div>
</section>
</main>

<footer>
  <div class="footer-band"></div>
  <div class="footer-brand">Step Out Studio</div>
  <div class="fsearch">Search website<b>GO</b></div>
  <div class="footer"></div>
  <div class="badges"><i style="top:12px"></i><i style="top:38px;background:#eee;border-color:#bbb"></i><i style="top:66px;left:30px;width:44px;height:26px;background:#ddd;border-color:#999"></i></div>
  <div class="fcol" style="left:228px"><h5>Company</h5>Home<br>About Us<br>Blog<br>Latest News<br>Login<br>Join Us</div>
  <div class="fcol" style="left:302px"><h5>Customers</h5>Register<br>Login<br>Manage Booking</div>
  <div class="fcol" style="left:395px"><h5>Businesses</h5>Register<br>Lisat a Class or Activity</div>
  <div class="fcol" style="left:504px"><h5>Information</h5>My Account<br>Rewards<br>Terms &amp; Conditions<br>Buying Guide<br>FAQ</div>
  <div class="fcol" style="left:615px"><h5>Social Network</h5>My Account<br>Rewards<br>Terms &amp; Conditions<br>Buying Guide<br>FAQ</div>
  <div class="fcol" style="left:732px"><h5>Contact Us</h5>Phone: 555.010.3377<br>Toll-Free: 555.010.3377<br>Fax: 555.010.3377<br>Email: <a href="#">Send us an email</a></div>
  <div class="copy">© 2011 stepoutstudio.example</div>
</footer>
</body>
</html>
```